SOLVE Study flyer

I need help designing a flyer for a research study that will include brain imaging in adolescents. The info is in the attached document. The study is called the Sequoia Outlook Lantern Valley Echo (SOLVE) study. Ideally this would be returned as a document that I can edit in the future as we will have several new recruitment phases (different age groups, etc. I also would love to have a logo designed as part of this project, but I recognize that might be a separate design request.

```html
<!DOCTYPE html>
<html lang="en">
<head>
<meta charset="utf-8">
<title>SOLVE Study – Recruitment Flyer</title>
<link href="https://fonts.googleapis.com/css2?family=Anton&family=Poppins:wght@400;500;600;700&display=swap" rel="stylesheet">
<style>
  :root{
    --purple:#4e1a60;
    --purple-deep:#54195e;
    --navy:#10205e;
    --navy-text:#1b2468;
    --gold:#f7bd28;
    --gold-box:#fcc12d;
    --hero-bg:#e5e7ef;
    --page-bg:#fafafa;
    --lavender:#efecf6;
    --icon-disc:#ede6ef;
    --elig-bg:#e9ecf6;
    --grey-text:#444;
  }
  *{box-sizing:border-box;margin:0;padding:0}
  html,body{width:927px;height:1200px;overflow:hidden;background:var(--page-bg)}
  body{font-family:"Poppins",sans-serif;position:relative}
  .flyer{position:relative;width:927px;height:1200px;overflow:hidden;background:var(--page-bg)}

  /* Hero */
  .hero{position:absolute;left:0;top:0;width:927px;height:489px;background:var(--hero-bg);overflow:hidden}
  .hero-photo{position:absolute;left:440px;top:126px;width:487px;height:363px;
    background:linear-gradient(90deg,rgba(229,231,239,1) 0%,rgba(232,220,214,0.9) 12%,#e9d6cf 35%,#c9a58e 70%,#8e6a58 100%)}
  .headline{position:absolute;left:29px;top:14px;font-family:"Anton",sans-serif;font-size:47px;line-height:54px;
    color:var(--purple);letter-spacing:1.5px}
  .headline-rule{position:absolute;left:29px;top:129px;width:316px;height:5px;background:var(--gold);border-radius:3px}
  .hero-question{position:absolute;left:29px;top:156px;font-size:29px;line-height:36px;font-weight:500;color:var(--navy-text)}
  .thought-bubble{position:absolute;left:333px;top:138px;width:122px;height:110px;border-radius:50%;
    background:rgba(255,255,255,0.35)}
  .bubble-dot{position:absolute;border:1.5px solid var(--navy);border-radius:50%}

  .badge{position:absolute;left:594px;top:-179px;width:434px;height:434px;border-radius:50%;background:var(--navy)}
  .badge-join{position:absolute;left:686px;top:20px;width:206px;text-align:center;color:#fff;font-size:21px;font-weight:500}
  .badge-join::before,.badge-join::after{content:"";position:absolute;top:14px;width:52px;height:2px;background:var(--gold)}
  .badge-join::before{left:0}.badge-join::after{right:0}
  .badge-name{position:absolute;left:678px;top:44px;width:222px;text-align:center;font-family:"Anton",sans-serif;
    font-size:74px;line-height:80px;color:#fff;letter-spacing:8px}
  .badge-study{position:absolute;left:676px;top:122px;width:226px;text-align:center;font-family:"Anton",sans-serif;
    font-size:45px;line-height:50px;color:var(--gold);letter-spacing:5px}
  .badge-study::before,.badge-study::after{content:"";position:absolute;top:24px;width:38px;height:2px;background:var(--gold)}
  .badge-study::before{left:0}.badge-study::after{right:0}
  .badge-fullname{position:absolute;left:672px;top:179px;width:234px;text-align:center;color:#fff;font-size:13.5px;line-height:19.5px}

  .intro-card{position:absolute;left:29px;top:290px;width:432px;height:177px;background:var(--lavender);
    border:1px solid #d6d2e0;border-radius:16px}
  .intro-icon{position:absolute;left:14px;top:54px;width:86px;height:70px}
  .intro-text{position:absolute;left:122px;top:30px;width:300px;font-size:14.2px;line-height:24.4px;color:var(--purple)}
  .intro-text strong{font-weight:600}

  /* Participation */
  .section-title{position:absolute;left:0;top:517px;width:927px;text-align:center;font-size:25px;font-weight:500;color:var(--navy-text)}
  .title-rule{position:absolute;top:536px;width:200px;height:2px;background:var(--purple)}
  .step{position:absolute;top:570px;width:280px;text-align:center}
  .step-disc{width:101px;height:101px;margin:0 auto;border-radius:50%;background:var(--icon-disc);display:flex;align-items:center;justify-content:center}
  .step-title{margin-top:7px;font-size:20px;font-weight:500;color:var(--purple)}
  .step-text{margin-top:2px;font-size:15px;line-height:18.4px;color:var(--grey-text)}
  .step-divider{position:absolute;top:570px;height:240px;border-left:1.5px dashed #777}

  /* Eligibility */
  .eligibility{position:absolute;left:29px;top:845px;width:869px;height:186px;background:var(--elig-bg);border-radius:14px;overflow:hidden}
  .elig-icon{position:absolute;left:22px;top:42px}
  .elig-title{position:absolute;left:171px;top:20px;font-size:26px;font-weight:500;color:var(--navy-text)}
  .elig-list{position:absolute;left:171px;top:65px;list-style:none;font-size:16px;line-height:19px;color:#3a3a4a}
  .elig-list li{position:relative;padding-left:29px;margin-bottom:10px}
  .elig-list svg{position:absolute;left:0;top:1px}
  .head-figure{position:absolute;left:700px;top:18px;width:120px;height:150px;border-radius:50% 50% 30% 40%;
    background:linear-gradient(160deg,rgba(84,25,94,0.10),rgba(84,25,94,0.04))}
  .head-baseline{position:absolute;left:512px;top:172px;width:357px;height:1.5px;background:var(--purple)}

  /* Footer boxes */
  .contact{position:absolute;left:27px;top:1036px;width:487px;height:154px;background:var(--purple-deep);border-radius:14px}
  .contact-icon{position:absolute;left:17px;top:44px}
  .box-divider{position:absolute;top:0;height:154px;border-left:1.5px dashed rgba(255,255,255,0.8)}
  .contact-heading{position:absolute;left:123px;top:14px;font-size:25px;line-height:30px;font-weight:500;color:#fff}
  .contact-prompt{position:absolute;left:122px;top:84px;font-size:16px;color:#fff}
  .contact-rule{position:absolute;left:289px;top:97px;width:136px;height:2px;background:var(--gold)}
  .contact-email{position:absolute;left:122px;top:102px;font-size:25.5px;font-weight:500;color:var(--gold)}

  .compensation{position:absolute;left:523px;top:1036px;width:375px;height:154px;background:var(--gold-box);border-radius:14px}
  .comp-icon{position:absolute;left:22px;top:40px}
  .compensation .box-divider{border-left-color:var(--navy)}
  .comp-label{position:absolute;left:155px;top:26px;font-size:27px;line-height:30px;font-weight:500;color:var(--navy)}
  .comp-amount{position:absolute;left:152px;top:88px;font-size:45px;line-height:50px;font-weight:700;color:var(--navy)}
</style>
</head>
<body>
<main class="flyer">

  <section class="hero">
    <div class="hero-photo" role="img" aria-label="Photo of a parent gently comforting a young daughter seated on a sofa"></div>

    <h1 class="headline">ARE YOU THE PARENT<br>OF A CHILD AGE 10-17?</h1>
    <div class="headline-rule"></div>

    <h2 class="hero-question">Do they worry or<br>overthink negative<br>emotions?</h2>
    <div class="thought-bubble" role="img" aria-label="Illustration of a thought bubble filled with a tangled scribble"></div>
    <span class="bubble-dot" style="left:345px;top:249px;width:19px;height:19px"></span>
    <span class="bubble-dot" style="left:331px;top:274px;width:13px;height:13px"></span>
    <span class="bubble-dot" style="left:318px;top:292px;width:8px;height:8px"></span>

    <div class="badge"></div>
    <div class="badge-join">Join the</div>
    <div class="badge-name">SOLVE</div>
    <div class="badge-study">STUDY</div>
    <p class="badge-fullname">Sequoia Outlook Lantern<br>Valley Echo<br>(SOLVE) Study</p>

    <div class="intro-card">
      <div class="intro-icon" role="img" aria-label="Line icon of a group of three girls"></div>
      <p class="intro-text">Northgate University researchers are seeking <strong>girls age 10–17</strong> for a study about brain activity in emotions &amp; decision - making and how they relate to puberty, anxiety and depression.</p>
    </div>
  </section>

  <h2 class="section-title">Study participation involves:</h2>
  <div class="title-rule" style="left:41px"></div>
  <div class="title-rule" style="left:686px"></div>

  <article class="step" style="left:23px">
    <div class="step-disc">
      <svg width="62" height="50" viewBox="0 0 62 50" fill="none" stroke="#4e1a60" stroke-width="1.8">
        <rect x="8" y="10" width="34" height="28" rx="2"/>
        <path d="M2 44h46l-4-6H6z"/>
        <circle cx="20" cy="20" r="4"/><path d="M13 32c1-6 13-6 14 0"/>
        <rect x="34" y="2" width="26" height="18" rx="2" fill="#ede6ef"/>
        <path d="M39 9h16M39 14h11"/>
      </svg>
    </div>
    <h3 class="step-title">One one-hour interview</h3>
    <p class="step-text">(online or in-person)<br>where your child will discuss their thoughts</p>
  </article>

  <div class="step-divider" style="left:313px"></div>

  <article class="step" style="left:323px">
    <div class="step-disc">
      <svg width="50" height="52" viewBox="0 0 50 52" fill="none" stroke="#4e1a60" stroke-width="1.8">
        <path d="M6 2h24l8 8v40H6z"/><path d="M30 2v8h8"/>
        <path d="M11 16h4M18 16h14M11 24h4M18 24h14M11 32h4M18 32h14M11 40h4M18 40h10"/>
        <path d="M34 46l12-14 3 3-12 14-4 1z"/>
      </svg>
    </div>
    <h3 class="step-title">Online questionnaires</h3>
    <p class="step-text">(parent and child)</p>
  </article>

  <div class="step-divider" style="left:613px"></div>

  <article class="step" style="left:624px">
    <div class="step-disc">
      <svg width="50" height="50" viewBox="0 0 50 50" fill="none" stroke="#4e1a60" stroke-width="1.8">
        <circle cx="25" cy="24" r="20"/><circle cx="25" cy="24" r="13"/>
        <circle cx="25" cy="20" r="4"/><path d="M16 32c2-6 16-6 18 0"/>
        <rect x="9" y="32" width="32" height="8" rx="1"/><path d="M12 40v6h26v-6"/>
        <rect x="21" y="2" width="8" height="4"/>
      </svg>
    </div>
    <h3 class="step-title">One two-hour visit</h3>
    <p class="step-text">where your child will complete an MRI scan, answer questions about their puberty stage, and have a small hair sample taken to study puberty hormones</p>
  </article>

  <section class="eligibility">
    <svg class="elig-icon" width="102" height="102" viewBox="0 0 102 102" fill="none" stroke="#10205e" stroke-width="2.6">
      <path d="M2 2h52l14 14v84H2z"/><path d="M54 2v14h14"/>
      <rect x="12" y="28" width="10" height="9"/><rect x="12" y="49" width="10" height="9"/><rect x="12" y="70" width="10" height="9"/>
      <path d="M28 32h20M28 53h14M28 74h18"/>
      <circle cx="61" cy="54" r="19" fill="#e9ecf6"/><circle cx="61" cy="54" r="12"/>
      <path d="M55 54l5 5 8-9"/><path d="M75 68l14 14-4 4-14-14"/>
    </svg>
    <h2 class="elig-title">Your child may be eligible if they:</h2>
    <ul class="elig-list">
      <li><svg width="17" height="17" viewBox="0 0 17 17"><circle cx="8.5" cy="8.5" r="8.5" fill="#10205e"/><path d="M4.5 8.7l2.7 2.6 5-5" stroke="#fff" stroke-width="1.8" fill="none"/></svg>Are age 10-17</li>
      <li><svg width="17" height="17" viewBox="0 0 17 17"><circle cx="8.5" cy="8.5" r="8.5" fill="#10205e"/><path d="M4.5 8.7l2.7 2.6 5-5" stroke="#fff" stroke-width="1.8" fill="none"/></svg>Tend to worry or overthink negative thoughts</li>
      <li><svg width="17" height="17" viewBox="0 0 17 17"><circle cx="8.5" cy="8.5" r="8.5" fill="#10205e"/><path d="M4.5 8.7l2.7 2.6 5-5" stroke="#fff" stroke-width="1.8" fill="none"/></svg>Have not been diagnosed with psychosis,<br>learning problems, or autism</li>
    </ul>
    <div class="head-figure" role="img" aria-label="Line illustration of a head in profile showing the brain"></div>
    <div class="head-baseline"></div>
  </section>

  <section class="contact">
    <svg class="contact-icon" width="66" height="66" viewBox="0 0 66 66" fill="none" stroke="#fff" stroke-width="2.4">
      <path d="M2 26l31-24 31 24v38H2z" fill="#fff"/>
      <rect x="12" y="10" width="42" height="34" fill="#54195e" stroke="#54195e"/>
      <path d="M2 26l31 22 31-22" stroke="#54195e"/>
      <circle cx="33" cy="24" r="9"/><circle cx="33" cy="24" r="4"/><path d="M37 20v6c0 3 5 3 5-2"/>
    </svg>
    <div class="box-divider" style="left:103px"></div>
    <h2 class="contact-heading">Interested in participating?<br>Want more information?</h2>
    <p class="contact-prompt">Please contact us!</p>
    <div class="contact-rule"></div>
    <p class="contact-email">solvestudy@northgate.edu</p>
  </section>

  <section class="compensation">
    <svg class="comp-icon" width="76" height="76" viewBox="0 0 76 76">
      <circle cx="44" cy="36" r="20" fill="#10205e"/>
      <path d="M38 12h12l-3 7h-6z" fill="#10205e"/>
      <text x="44" y="44" text-anchor="middle" font-family="Poppins,sans-serif" font-size="20" font-weight="700" fill="#fcc12d">$</text>
      <rect x="2" y="50" width="9" height="20" fill="#10205e"/>
      <path d="M13 54h18c4 0 6 4 2 5h-10m10 0l22-6c4-1 6 3 2 5l-26 10H13" fill="none" stroke="#10205e" stroke-width="3"/>
    </svg>
    <div class="box-divider" style="left:127px"></div>
    <p class="comp-label">Compensation<br>up to</p>
    <p class="comp-amount">$140</p>
  </section>

</main>
</body>
</html>
```